Wordpress Template Design using existing Logo and Colors

We are wanting a wordpress theme designing for our b2b marketing consultancy business. A comprehesive and elagant design to our current site www.plovtrix.com would be good.

Industry/Entity Type

Marketing

Font styles to use
Sans Serif

```html
<!DOCTYPE html>
<html lang="en">
<head>
<meta charset="utf-8">
<title>Plovtrix — B2B Data, Analytics and Marketing</title>
<link href="https://fonts.googleapis.com/css2?family=Montserrat:wght@400;500;600;700&family=Open+Sans:ital,wght@0,400;0,600;1,400&display=swap" rel="stylesheet">
<style>
:root{
  --red:#e4202a;
  --slate:#4d5566;
  --navy:#1a2236;
  --ink:#3a3f4b;
  --muted:#666b75;
  --grey-band:#e6e6e6;
  --line:#d4d6da;
  --white:#ffffff;
}
*{box-sizing:border-box;margin:0;padding:0}
html,body{width:1200px;height:3273px;overflow:hidden}
body{font-family:"Open Sans",Arial,sans-serif;color:var(--ink);background:var(--white);position:relative}
section,header,footer{position:absolute;left:0;width:1200px}
.abs{position:absolute}

/* hero */
.hero{top:0;height:659px;overflow:hidden}
.hero-photo{position:absolute;inset:0;background:linear-gradient(120deg,#3c3a38 0%,#6b6158 35%,#2e2b2a 65%,#55504a 100%)}
.hero-shade{position:absolute;inset:0;background:rgba(0,0,0,.35)}
.brand{position:absolute;left:128px;top:46px;font-family:"Montserrat",Arial,sans-serif;font-weight:700;font-size:34px;letter-spacing:3px;color:var(--white)}
.nav{position:absolute;top:52px;right:130px;display:flex;align-items:center;gap:28px;font-family:"Montserrat",Arial,sans-serif;font-weight:600;font-size:13px;letter-spacing:.5px;color:var(--white)}
.nav .cta{background:var(--red);padding:11px 18px}
.hero-title{position:absolute;top:282px;width:100%;text-align:center;font-family:"Montserrat",Arial,sans-serif;font-weight:700;font-size:40px;line-height:52px;color:var(--white);letter-spacing:.5px}
.dots{position:absolute;top:606px;left:0;width:100%;display:flex;justify-content:center;gap:8px}
.dots span{width:14px;height:14px;border-radius:50%;background:var(--white)}
.dots span.on{background:transparent;border:2px solid var(--white)}

/* section heading */
.heading{position:absolute;left:0;width:100%;text-align:center}
.heading h2{font-family:"Montserrat",Arial,sans-serif;font-weight:600;font-size:26px;color:var(--slate);letter-spacing:.5px;display:inline-block;padding:0 18px 8px;border-bottom:2px solid var(--line)}
.heading i{display:block;width:7px;height:7px;background:var(--red);margin:4px auto 0}

/* about */
.about{top:659px;height:395px}
.about p{position:absolute;top:162px;left:160px;width:880px;text-align:center;font-size:16px;line-height:28px;color:var(--muted)}
.btn{position:absolute;display:flex;align-items:center;justify-content:center;font-family:"Montserrat",Arial,sans-serif;font-weight:500;font-size:14px}
.btn-solid{background:var(--slate);color:var(--white)}
.btn-outline{border:2px solid var(--red);color:var(--red)}
.btn-line{border:2px solid var(--slate);color:var(--ink);font-size:13px}
.btn-line.light{border-color:var(--white);color:var(--white)}

/* services */
.services{top:1054px;height:552px;background:var(--grey-band)}
.card{position:absolute;top:140px;width:310px;height:364px;background:var(--white);box-shadow:0 1px 4px rgba(0,0,0,.15);text-align:center}
.card .pic{height:188px}
.card .badge{position:absolute;top:164px;left:131px;width:48px;height:48px;background:var(--red);display:flex;align-items:center;justify-content:center}
.card h3{margin-top:40px;font-family:"Montserrat",Arial,sans-serif;font-weight:500;font-size:20px;color:var(--red)}
.card p{margin:8px 30px 0;font-size:13px;line-height:19px;color:var(--muted)}
.card .more{display:block;margin-top:6px;font-family:"Montserrat",Arial,sans-serif;font-size:13px;font-weight:500;color:var(--ink)}

/* feature rows */
.feature-title{font-family:"Montserrat",Arial,sans-serif;font-weight:500;font-size:26px;color:var(--slate)}
.feature-text{font-size:14px;line-height:26px;color:var(--muted)}
.feature-copy{position:absolute;z-index:2}
.target{top:1606px;height:406px}
.datamgmt{top:2012px;height:410px;background:linear-gradient(100deg,#e4202a 0%,#c42a3a 40%,#8a3d55 70%,#4d5a72 100%)}
.datamgmt .feature-title,.datamgmt .feature-text{color:var(--white)}

/* testimonials */
.testimonials{top:2422px;height:480px}
.quote{position:absolute;top:155px;width:310px;height:185px;border:2px solid var(--line);text-align:center;padding:20px 22px 0}
.quote .mark{font-family:"Montserrat",Arial,sans-serif;font-weight:700;font-size:40px;line-height:40px;color:var(--slate)}
.quote p{margin-top:10px;font-style:italic;font-size:13px;line-height:23px;color:var(--muted)}
.author{position:absolute;top:362px;display:flex;align-items:center;gap:8px}
.author .face{width:42px;height:42px;border-radius:50%}
.author b{display:block;font-family:"Open Sans",Arial,sans-serif;font-weight:400;font-size:16px;color:var(--slate)}
.author small{font-size:12px;color:var(--muted)}
.arrow{position:absolute;top:231px}

/* footer */
.site-footer{top:2902px;height:371px;background:var(--navy);color:var(--white)}
.col{position:absolute;top:70px}
.col h4{font-family:"Montserrat",Arial,sans-serif;font-weight:500;font-size:17px;margin-bottom:18px;letter-spacing:.3px}
.col li{list-style:none;font-size:13px;line-height:28px}
.col .row{display:flex;gap:10px;font-size:13px;line-height:20px;margin-bottom:10px}
.col .plain{font-size:13px;line-height:20px;margin-bottom:12px}
.rule{position:absolute;left:146px;width:908px;top:277px;border-top:1px solid #3a4258}
.copy{position:absolute;left:148px;top:297px;font-size:12px;color:#c5c9d3}
.social{position:absolute;right:148px;top:290px;display:flex;gap:6px}
.social span{width:28px;height:28px;border-radius:50%;border:1.5px solid var(--white)}
</style>
</head>
<body>

<header class="hero">
  <div class="hero-photo" role="img" aria-label="Photo of a busy open-plan office with a team working at computers"></div>
  <div class="hero-shade"></div>
  <div class="brand">PLOVTRIX</div>
  <nav class="nav">
    <span>TARGET MARKETING</span>
    <span>DATA MANAGEMENT</span>
    <span>ABOUT US</span>
    <span class="cta">CONTACT US</span>
  </nav>
  <h1 class="hero-title">BETTER DATA, BETTER TARGET,<br>BETTER RESULTS</h1>
  <div class="dots"><span class="on"></span><span></span><span></span><span></span></div>
</header>

<section class="about">
  <div class="heading" style="top:90px"><h2>ABOUT COMPANY</h2><i></i></div>
  <p>We are a B2B Data, Analytics and Marketing Consulting Company specialized in harnessing the power of potential data to strengthen connections between decisions makers, companies and products. We focus on solutions engineered to solve distinct challenges in the data, direct marketing, and analytics space.</p>
  <div class="btn btn-solid" style="left:375px;top:276px;width:210px;height:44px">LEARN MORE</div>
  <div class="btn btn-outline" style="left:598px;top:276px;width:210px;height:44px">BROCHURE DOWNLOAD</div>
</section>

<section class="services">
  <div class="heading" style="top:64px"><h2>OUR SERVICES</h2><i></i></div>

  <div class="card" style="left:120px">
    <div class="pic" role="img" aria-label="Photo of a hand touching a glowing digital data screen" style="background:linear-gradient(135deg,#0d1d3a,#1f4a7a 55%,#0f2a4c)"></div>
    <div class="badge"><svg width="26" height="26" viewBox="0 0 26 26" fill="none" stroke="#fff" stroke-width="2"><rect x="3" y="16" width="7" height="7"/><rect x="16" y="16" width="7" height="7"/><rect x="9.5" y="3" width="7" height="7"/><path d="M13 10v3M6.5 16v-3h13v3"/></svg></div>
    <h3>B2B SERVICES</h3>
    <p>Ut nisi erat fermentum vel congue id euismod in elit Fusce ultricies orci ac feugiat suscipit leo massa</p>
    <span class="more">READ MORE</span>
  </div>

  <div class="card" style="left:445px">
    <div class="pic" role="img" aria-label="Photo of call centre staff wearing headsets" style="background:linear-gradient(135deg,#d8dde3,#b9c2cc 50%,#e9ecef)"></div>
    <div class="badge"><svg width="24" height="24" viewBox="0 0 24 24" fill="none" stroke="#fff" stroke-width="2" stroke-linejoin="round"><path d="M5 3h4l2 5-2.5 1.5a11 11 0 0 0 6 6L16 13l5 2v4a2 2 0 0 1-2 2A17 17 0 0 1 3 5a2 2 0 0 1 2-2z"/></svg></div>
    <h3>CALL CENTRE</h3>
    <p>Ut nisi erat fermentum vel congue id euismod in elit Fusce ultricies orci ac feugiat suscipit leo massa</p>
    <span class="more">READ MORE</span>
  </div>

  <div class="card" style="left:770px">
    <div class="pic" role="img" aria-label="Photo of parcels and a globe on a laptop keyboard" style="background:linear-gradient(135deg,#8c7d68,#c9b89a 50%,#5d5f66)"></div>
    <div class="badge"><svg width="26" height="26" viewBox="0 0 26 26" fill="none" stroke="#fff" stroke-width="2" stroke-linejoin="round"><path d="M3 10h5l10-6v18L8 16H3z"/><path d="M6 16l2 6h3l-1-6"/></svg></div>
    <h3>MARKETING AUTOMATION</h3>
    <p>Ut nisi erat fermentum vel congue id euismod in elit Fusce ultricies orci ac feugiat suscipit leo massa</p>
    <span class="more">READ MORE</span>
  </div>
</section>

<section class="target">
  <div class="abs" role="img" aria-label="Line illustration of a target with arrows, documents and charts" style="left:566px;top:46px;width:514px;height:264px;background:radial-gradient(ellipse at 60% 45%,#dbe8f7 0%,#eef4fb 55%,#ffffff 80%)"></div>
  <div class="feature-copy" style="left:152px;top:84px;width:410px">
    <h2 class="feature-title">TARGET MARKETING</h2>
    <p class="feature-text" style="margin-top:12px">Vivamus porttitor purus nisi eleifend libero a tempus libero lectus feugiat felis Morbi diam mauris viverra in gravida eu mattis in ante Morbi eget arcu Morbi porta libero id ullamcorper nonummy nibh ligula pulvinar</p>
  </div>
  <div class="btn btn-line" style="left:158px;top:251px;width:132px;height:36px">READ MORE</div>
</section>

<section class="datamgmt">
  <div class="abs" role="img" aria-label="Line illustration of data charts, graphs and documents" style="left:110px;top:28px;width:512px;height:306px;background:radial-gradient(ellipse at 50% 50%,rgba(255,255,255,.32) 0%,rgba(255,255,255,.12) 55%,rgba(255,255,255,0) 80%)"></div>
  <div class="feature-copy" style="left:670px;top:94px;width:410px">
    <h2 class="feature-title">DATA MANAGEMENT</h2>
    <p class="feature-text" style="margin-top:12px">Vivamus porttitor purus nisi eleifend libero a tempus libero lectus feugiat felis Morbi diam mauris viverra in gravida eu mattis in ante Morbi eget arcu Morbi porta libero id ullamcorper nonummy nibh ligula pulvinar</p>
  </div>
  <div class="btn btn-line light" style="left:672px;top:248px;width:132px;height:36px">READ MORE</div>
</section>

<section class="testimonials">
  <div class="heading" style="top:80px"><h2>TESTIMONIALS</h2><i></i></div>

  <svg class="arrow" style="left:80px" width="18" height="30" viewBox="0 0 18 30" fill="none" stroke="#8a8f99" stroke-width="3"><path d="M15 2L3 15l12 13"/></svg>
  <svg class="arrow" style="left:1094px" width="18" height="30" viewBox="0 0 18 30" fill="none" stroke="#8a8f99" stroke-width="3"><path d="M3 2l12 13L3 28"/></svg>

  <div class="quote" style="left:120px"><div class="mark">&ldquo;</div><p>In ullamcorper est eget tempor cursus neque mi consectetuer mi a ultricies massa est sed nisl Class aptent taciti sociosqu ad litora torquent per conubia nostra</p></div>
  <div class="quote" style="left:445px"><div class="mark">&ldquo;</div><p>In ullamcorper est eget tempor cursus neque mi consectetuer mi a ultricies massa est sed nisl Class aptent taciti sociosqu ad litora torquent per conubia nostra</p></div>
  <div class="quote" style="left:775px"><div class="mark">&ldquo;</div><p>In ullamcorper est eget tempor cursus neque mi consectetuer mi a ultricies massa est sed nisl Class aptent taciti sociosqu ad litora torquent per conubia nostra</p></div>

  <div class="author" style="left:198px"><div class="face" role="img" aria-label="Client portrait" style="background:#c9a89a"></div><div><b>By Author Name</b><small>City, Location</small></div></div>
  <div class="author" style="left:522px"><div class="face" role="img" aria-label="Client portrait" style="background:#9a8e86"></div><div><b>By Author Name</b><small>City, Location</small></div></div>
  <div class="author" style="left:854px"><div class="face" role="img" aria-label="Client portrait" style="background:#a8917d"></div><div><b>By Author Name</b><small>City, Location</small></div></div>
</section>

<footer class="site-footer">
  <div class="col" style="left:131px"><h4>COMPANY</h4><ul><li>Home</li><li>About</li><li>Our Services</li><li>Support</li></ul></div>
  <div class="col" style="left:310px"><h4>RESOURCES</h4><ul><li>Testimonials</li><li>Marketing Automation</li><li>Contact Us</li></ul></div>
  <div class="col" style="left:528px;width:250px"><h4>GLOBAL HQ</h4>
    <div class="row"><svg width="12" height="16" viewBox="0 0 12 16" fill="#fff"><path d="M6 0a6 6 0 0 0-6 6c0 4.5 6 10 6 10s6-5.5 6-10a6 6 0 0 0-6-6zm0 8.5A2.5 2.5 0 1 1 6 3.5a2.5 2.5 0 0 1 0 5z"/></svg><span>4120 Harlow Avenue, Suite 208,<br>Marvale, CA 90415-2200, USA</span></div>
    <div class="row"><svg width="13" height="13" viewBox="0 0 24 24" fill="#fff"><path d="M5 2h4l2 5-2.5 1.5a11 11 0 0 0 6 6L16 12l5 2v4a2 2 0 0 1-2 2A17 17 0 0 1 3 4a2 2 0 0 1 2-2z"/></svg><span>+1 (555) 410-2386</span></div>
    <div class="row"><svg width="14" height="11" viewBox="0 0 14 11" fill="#fff"><path d="M0 0h14v1.5L7 6 0 1.5z"/><path d="M0 3l7 4.5L14 3v8H0z"/></svg><span>contactus.us@plovtrix.com</span></div>
  </div>
  <div class="col" style="left:816px;width:250px"><h4>REGIONAL HQ</h4>
    <div class="plain">18 Kestrel Lane 2, #07-04 Arden<br>Park, Singapore 400512</div>
    <div class="plain">+65 6000 4172</div>
    <div class="plain">contactus.sg@plovtrix.com</div>
  </div>
  <div class="rule"></div>
  <div class="copy">© 2018 Company Name &nbsp;All right reserved</div>
  <div class="social"><span></span><span></span><span></span><span></span></div>
</footer>

</body>
</html>
```